Professional, Upmarket, Gas Station Card Design for a Company

Design for a 2-sided Fuel Card for Dravon Service Stations
Front Design
Has the Dravon Logo and Company Logo
Will have the Card Numbers display
Will have Vehicle Rego Display
Will have Expiry Date

Back Design
Will have a magnetic strip at the bottom of the card
will have a list of service stations the card is valid
will have address of return should the card be lost and found

The card should be blue in color - Dravon Blue
Should have a faded motif design of water droplet

Target Market(s)

Corporate Clients

Industry/Entity Type

Oil and Gas

Font styles to use
Serif

Colors
0054AA
0677BA
7BADD7
CADEEF
E8F1F8

Requirements
Must have
• Dravon Logo, KelFuel Logo, Motif, Magnetic strips
Nice to have
• black color alternative, faded card, traditional design motif, water motif

```html
<!DOCTYPE html>
<html lang="en">
<head>
<meta charset="utf-8">
<title>Dravon Fuel Card</title>
<link rel="stylesheet" href="https://fonts.googleapis.com/css2?family=Roboto:wght@400;500;700&display=swap">
<style>
  :root {
    --page: #ffffff;
    --navy-deep: #020c3a;
    --navy: #06237a;
    --blue: #0a3fb0;
    --blue-bright: #0677ba;
    --streak: #cadeef;
    --ink: #ffffff;
    --brand-blue: #0054aa;
    --brand-red: #b0122a;
    --strip: #000000;
  }
  * { box-sizing: border-box; margin: 0; padding: 0; }
  html, body { width: 1200px; height: 559px; overflow: hidden; background: var(--page); }
  body { position: relative; font-family: "Roboto", Arial, sans-serif; color: var(--ink); }

  .card {
    position: absolute;
    border-radius: 30px;
    overflow: hidden;
    background:
      linear-gradient(135deg, transparent 42%, rgba(202,222,239,0.15) 47%, rgba(232,241,248,0.75) 50%, rgba(202,222,239,0.15) 53%, transparent 58%),
      radial-gradient(ellipse at 60% 45%, var(--blue) 0%, var(--navy) 50%, var(--navy-deep) 100%);
  }
  .card--front { left: 68px; top: 100px; width: 533px; height: 320px; }
  .card--back {
    left: 625px; top: 103px; width: 529px; height: 318px;
    background:
      linear-gradient(225deg, transparent 30%, rgba(202,222,239,0.15) 37%, rgba(232,241,248,0.75) 40%, rgba(202,222,239,0.15) 43%, transparent 50%),
      radial-gradient(ellipse at 45% 40%, var(--blue) 0%, var(--navy) 50%, var(--navy-deep) 100%);
  }

  .brand-name {
    position: absolute; left: 65px; top: 22px;
    font-weight: 700; font-size: 38px; letter-spacing: -0.5px;
    color: var(--brand-blue);
  }
  .partner-badge {
    position: absolute; width: 98px; height: 98px; border-radius: 50%;
    background: #ffffff;
    display: flex; align-items: center; justify-content: center;
    font-weight: 700; font-size: 19px; color: var(--brand-red);
  }
  .card--front .partner-badge { left: 400px; top: 28px; }
  .card--back .partner-badge { left: 218px; top: 38px; }

  .card-number {
    position: absolute; left: 62px; top: 158px;
    font-size: 42px; font-weight: 400; letter-spacing: 1.5px; white-space: nowrap;
  }
  .vehicle-rego { position: absolute; left: 62px; top: 226px; font-size: 16px; }
  .expiry { position: absolute; left: 367px; top: 230px; display: flex; align-items: center; gap: 6px; }
  .expiry-label { font-size: 15px; line-height: 15px; text-align: center; }
  .expiry-arrow { width: 0; height: 0; border-top: 5px solid transparent; border-bottom: 5px solid transparent; border-left: 6px solid var(--ink); }
  .expiry-date { font-size: 18px; letter-spacing: 0.5px; }
  .cardholder { position: absolute; left: 62px; top: 273px; font-size: 20px; letter-spacing: 0.3px; }

  .card-terms { position: absolute; left: 63px; top: 149px; width: 430px; font-size: 6.6px; line-height: 9px; color: #dfe8f6; }
  .card-terms p + p { margin-top: 7px; }
  .mag-strip { position: absolute; left: 0; top: 212px; width: 100%; height: 75px; background: var(--strip); }
</style>
</head>
<body>
  <section class="card card--front" aria-label="Dravon fuel card, front">
    <div class="brand-name">Dravon</div>
    <div class="partner-badge">KelFuel</div>
    <div class="card-number">1234 5678 9012 3456</div>
    <div class="vehicle-rego">GVR223</div>
    <div class="expiry">
      <div class="expiry-label">VALID<br>THRU</div>
      <span class="expiry-arrow"></span>
      <div class="expiry-date">01/24</div>
    </div>
    <div class="cardholder">CARDHOLDER NAME</div>
  </section>

  <section class="card card--back" aria-label="Dravon fuel card, back">
    <div class="partner-badge">KelFuel</div>
    <div class="card-terms">
      <p>Lorem ipsum dolor sit amet, consectetur adipiscing elit. Fusce dignissim pretium consectetur. Curabitur tempor posuere massa in varius. Pellentesque viverra nibh eu vehicula mattis. Nullam porta facilisis justo, a feugiat dolor sodales sed.</p>
      <p>Lorem ipsum dolor sit amet, consectetur adipiscing elit. Fusce dignissim pretium consectetur. Curabitur tempor posuere massa in varius. Pellentesque viverra nibh eu vehicula mattis. Nullam porta facilisis justo, a feugiat dolor sodales sed.</p>
    </div>
    <div class="mag-strip"></div>
  </section>
</body>
</html>
```